KVB Website

We need a website for a company based in Doha Qatar called Brightpath Talent Global. It is a global recruitment company, that specializes in both mass recruitment and headhunting. The company is the number 1 one stop shop for recruitment in Qatar. It recruits from all over the world Europe, Asia, Americas, Middle East, Africa for Qatar.

Target Market(s)

Multinational companies, fortune 500 company CEO's, any top earning companies that are looking for a large number of employees or headhunting employees.
Also for candidates looking for companies to work in Qatar.

Industry/Entity Type

Shop

Colors
ffffff

Requirements
Must have
• Most important qualities the website needs to have:
Clean
Modern
Elegant
Professional
Less Tabs
Minimalisitc

Some examples, I would like you to follow are here:
http://www.velmora.ca/
http://www.trovenkip.com/
https://quelbrandix.com/match#

The main color should be white and it has to have a very stylish, modern and cool look. While being minimalistic. I do not want too many tabs. I want it to be simplistic to understand. the only place where the pink logo color is should be in the logo. The logo color should not be anywhere else. It has to be absolutely sleek. Please follow the example websites that I have provided.

I will send the contact details you need to add later. There is no need for a log in page.

Whatever you think that may be important for a recruitment site do suggest. But there is no need for a log in area as we are a different kind of recruitment company.

There should be an area for testimonials from clients. There should also be an area for news flash for the latest countries we are hiring from and the latest companies we are hiring for and the latest positions we are looking for.

Show me the best please. Whoever gives me the best, I will give them an order for the 2nd website too.

Nice to have
• I have included a powerpoint to explain more!

```html
<!DOCTYPE html>
<html lang="en">
<head>
<meta charset="utf-8">
<title>Brightpath Talent Global</title>
<link rel="stylesheet" href="https://fonts.googleapis.com/css2?family=Roboto+Condensed:wght@400;700&family=Alegreya+Sans:wght@400;500;700&display=swap">
<style>
:root{
  --logo-pink:#c4257f;
  --accent:#2f2f2f;
  --accent-top:#4a4a4a;
  --accent-bottom:#262626;
  --ink:#333;
  --muted:#777;
  --line:#e2e2e2;
  --grey-bg:#f4f4f4;
  --footer-bottom:#151515;
}
*{margin:0;padding:0;box-sizing:border-box}
html,body{width:732px;height:1200px;overflow:hidden;background:#fff}
body{position:relative;font-family:"Alegreya Sans",sans-serif;color:var(--ink);font-variant-numeric:lining-nums}
.abs{position:absolute}

/* top bar */
.topbar{left:0;top:0;width:732px;height:32px;border-bottom:1px solid var(--line);box-shadow:0 1px 2px rgba(0,0,0,.06)}
.topbar .cell{top:0;height:32px;display:flex;align-items:center;font-size:9px;color:#444;gap:6px}
.topbar .divider{top:0;width:1px;height:32px;background:var(--line)}
.social-dot{width:18px;height:18px;border:1px solid #aaa;border-radius:50%}
.flag{width:10px;height:7px;top:12px}

/* header */
.brand{left:61px;top:36px;width:120px;height:72px}
.brand-mark{left:16px;top:0;width:24px;height:24px;border-radius:50%;background:var(--logo-pink)}
.brand-name{left:0;top:30px;font-family:"Roboto Condensed",sans-serif;font-weight:700;font-size:10px;line-height:11px;color:var(--logo-pink);letter-spacing:.2px}
.header-links{right:62px;top:65px;font-size:9px;color:#444}

/* nav */
.nav{left:0;top:110px;width:732px;height:31px;background:linear-gradient(var(--accent-top),var(--accent-bottom))}
.nav ul{list-style:none;display:flex;position:absolute;left:61px;top:0;height:31px}
.nav li{font-family:"Roboto Condensed",sans-serif;font-size:9.5px;color:#fff;height:31px;line-height:31px;padding:0 9px;margin-right:12px}
.nav li.active{background:#111;margin-right:10px}

/* hero */
.hero{left:0;top:141px;width:732px;height:202px;background:linear-gradient(100deg,#8d8f95 0%,#b9bcc2 30%,#6f737b 55%,#a4a8ae 80%,#7d8087 100%)}
.hero-caption{left:62px;top:209px;width:411px;height:64px;background:rgba(60,60,60,.55);padding:8px 13px}
.hero-caption h1{font-family:"Roboto Condensed",sans-serif;font-weight:400;font-size:19px;color:#fff;letter-spacing:.3px}
.hero-caption p{font-family:"Roboto Condensed",sans-serif;font-size:11px;color:#e4e4e4;margin-top:7px}
.hero-next{right:0;top:214px;width:37px;height:37px;background:#222}

/* columns */
.col-head{top:363px;height:28px;background:linear-gradient(var(--accent-top),var(--accent-bottom));color:#fff;font-family:"Roboto Condensed",sans-serif;font-size:10px;line-height:28px;padding-left:12px}
.col-photo{top:403px;height:86px}
.col-text{top:499px;font-size:8.3px;line-height:15.2px;color:#666}
.more{top:529px;font-size:8.3px;line-height:15.2px;color:var(--accent);font-weight:700}
.field{left:268px;width:197px;height:28px;border:1px solid #ececec;box-shadow:inset 0 2px 3px rgba(0,0,0,.06);font-size:8.5px;color:#aaa;padding-left:12px;line-height:28px}
.btn{background:linear-gradient(var(--accent-top),var(--accent-bottom));color:#fff;font-size:8.5px;text-align:center;font-weight:500}

/* news band */
.band{left:0;top:576px;width:732px;height:264px;background:var(--grey-bg)}
.sec-title{font-size:15px;color:#333}
.sec-title b{color:#111;font-weight:700}
.date{width:22px}
.date .day{height:20px;background:#fff;text-align:center;font-weight:700;font-size:11px;color:var(--accent);line-height:20px}
.date .mon{height:11px;background:var(--accent);color:#fff;font-size:7px;text-align:center;line-height:11px}
.news-title{font-size:10.5px;line-height:15.5px;color:#333}
.news-body{font-size:7.6px;line-height:15.2px;color:#777}
.round-arrow{width:15px;height:15px;border-radius:50%;background:#8a8a8a}
.quote{left:461px;top:629px;width:209px;height:133px;background:linear-gradient(var(--accent-bottom),#555);border-radius:5px;padding:19px 16px 0 19px;color:#fff;font-size:8.3px;line-height:19.2px;text-indent:13px}
.quote-mark{left:470px;top:635px;font-size:24px;font-family:Georgia,serif;color:#fff;line-height:24px}

/* clients */
.client{top:898px;height:38px;display:flex;align-items:center;gap:5px;font-weight:700;font-size:21px;color:#222;white-space:nowrap}
.client .dot{width:16px;height:16px;border-radius:50%;background:#222}
.sq-arrow{top:861px;width:19px;height:18px}

/* footer */
.footer{left:0;top:969px;width:732px;height:171px;background:linear-gradient(#313131,#1b1b1b)}
.foot-head{top:1000px;font-family:"Roboto Condensed",sans-serif;font-size:10px;color:#fff}
.foot-text{font-size:7.6px;line-height:11.6px;color:#e0e0e0}
.foot-post{font-size:8.6px;line-height:15.2px;color:#ddd}
.foot-date{font-size:7.2px;color:#ccc}
.foot-social{top:1019px;width:17px;height:17px;border-radius:50%;background:#f2f2f2}
.foot-btn{background:linear-gradient(#6a6a6a,#4a4a4a)}
.copyright{left:0;top:1140px;width:732px;height:60px;background:var(--footer-bottom);font-size:7.4px;color:#888;text-align:center;line-height:60px}
</style>
</head>
<body>

<!-- top bar -->
<div class="abs topbar">
  <div class="abs divider" style="left:60px"></div>
  <div class="abs cell" style="left:71px">
    <svg width="8" height="8" viewBox="0 0 10 10"><path d="M2 0.5l2 2-1 1.3c.6 1.3 1.7 2.4 3 3l1.3-1 2 2-1.3 1.7C4.5 9.3.7 5.5.3 2z" fill="#555"/></svg>
    <span>+974 – 40001234</span>
  </div>
  <div class="abs divider" style="left:167px"></div>
  <div class="abs cell" style="left:178px">
    <svg width="9" height="7" viewBox="0 0 10 8"><rect width="10" height="8" fill="#555"/><path d="M0 0l5 4 5-4" stroke="#fff" fill="none"/></svg>
    <span>info@brightpathtalent.com</span>
  </div>
  <div class="abs divider" style="left:331px"></div>
  <div class="abs cell" style="left:344px;gap:4px">
    <span class="social-dot"></span><span class="social-dot"></span><span class="social-dot"></span><span class="social-dot"></span>
  </div>
  <div class="abs flag" style="left:617px;background:#2c4b94"></div>
  <div class="abs flag" style="left:636px;background:#c8c8d8"></div>
  <svg class="abs" style="left:661px;top:10px" width="11" height="11" viewBox="0 0 11 11"><circle cx="4.5" cy="4.5" r="3.4" stroke="#444" stroke-width="1.4" fill="none"/><path d="M7 7l3 3" stroke="#444" stroke-width="1.6"/></svg>
</div>

<!-- header -->
<div class="abs brand">
  <div class="abs brand-mark"></div>
  <div class="abs brand-name">BRIGHTPATH<br>TALENT GLOBAL</div>
</div>
<div class="abs header-links">Employers</div>

<!-- nav -->
<nav class="abs nav">
  <ul>
    <li class="active">Home</li><li>About us</li><li>Services</li><li>Picture Gallery</li><li>News</li><li>Jobs Search</li><li>Contact Us</li>
  </ul>
</nav>

<!-- hero -->
<div class="abs hero" role="img" aria-label="Photo of two business people shaking hands"></div>
<div class="abs hero-caption">
  <h1>Qatar Recruitment Company</h1>
  <p>Jobs in Doha, Qatar Employment Opportunity, International Recruitment Agencies</p>
</div>
<div class="abs hero-next"><svg width="37" height="37" viewBox="0 0 37 37"><path d="M16 12l7 6.5-7 6.5" stroke="#fff" stroke-width="1.6" fill="none"/></svg></div>

<!-- three columns -->
<div class="abs col-head" style="left:60px;width:198px">What we do</div>
<div class="abs col-head" style="left:268px;width:197px">Search Jobs</div>
<div class="abs col-head" style="left:473px;width:197px">Services</div>

<div class="abs col-photo" style="left:60px;width:198px;background:linear-gradient(90deg,#c9b6a6,#e8d8c8 50%,#bfb1a4)" role="img" aria-label="Photo of a smiling group of young professionals"></div>
<div class="abs col-text" style="left:60px;width:190px">Brightpath Talent Global offers a Qatar-based service, specializing in the recruitment of high caliber staff and provides advice</div>
<div class="abs more" style="left:212px">Read More</div>

<div class="abs field" style="top:402px">Enter Your Category</div>
<div class="abs field" style="top:438px">Enter Your Name</div>
<div class="abs field" style="top:476px">Enter Your Mail Id</div>
<div class="abs btn" style="left:268px;top:514px;width:58px;height:27px;line-height:27px">Search</div>

<div class="abs col-photo" style="left:474px;width:197px;background:linear-gradient(90deg,#6d6660,#b9aea4 50%,#4c4a4c)" role="img" aria-label="Photo of staff working together in an office"></div>
<div class="abs col-text" style="left:474px;width:192px">We can meet staffing requirements including management positions, front of house staff, back of house staffboth permanent</div>
<div class="abs more" style="left:625px">Read More</div>

<!-- news band -->
<div class="abs band"></div>
<div class="abs sec-title" style="left:60px;top:596px">Latest <b>News</b></div>

<div class="abs date" style="left:59px;top:632px"><div class="day">09</div><div class="mon">Jul</div></div>
<div class="abs news-title" style="left:95px;top:629px;width:160px">DUNEMARK AIRWAYS SSP - Recruitment Drive India</div>
<div class="abs news-body" style="left:95px;top:676px;width:162px">We, Brightpath Talent Global, the most trusted partner in recruitment solutions for Dunemark Airways SSP hereby announces the Talent Hunt, India.<br>BTG with its partner agency M/s R. T. Ventures in India are delighted to declare the pre selection dates stated as under:</div>
<div class="abs btn" style="left:95px;top:795px;width:65px;height:24px;line-height:24px">Read More</div>

<div class="abs date" style="left:264px;top:636px"><div class="day">08</div><div class="mon">Jul</div></div>
<div class="abs news-title" style="left:294px;top:629px;width:160px">DUNEMARK AIRWAYS SSP - Recruitment Drive India</div>
<div class="abs news-body" style="left:294px;top:676px;width:162px">We, Brightpath Talent Global, the most trusted partner in recruitment solutions for Dunemark Airways SSP hereby announces the Talent Hunt, India.<br>BTG with its partner agency M/s R. T. Ventures in India are delighted to declare the pre selection dates stated as under:</div>
<div class="abs btn" style="left:293px;top:795px;width:65px;height:24px;line-height:24px">Read More</div>

<div class="abs sec-title" style="left:461px;top:596px">What <b>Client's</b> Say</div>
<div class="abs round-arrow" style="left:637px;top:597px"><svg width="15" height="15" viewBox="0 0 15 15"><path d="M8.5 4.5l-3 3 3 3" stroke="#fff" stroke-width="1.6" fill="none"/></svg></div>
<div class="abs round-arrow" style="left:655px;top:597px"><svg width="15" height="15" viewBox="0 0 15 15"><path d="M6.5 4.5l3 3-3 3" stroke="#fff" stroke-width="1.6" fill="none"/></svg></div>
<div class="abs quote">Lorem ipsum dolor sit amet, consectetur adipiscing elit. Donec hendrerit vehicula est, in consequat. Lorem ipsum dolor sit amet, consecte-tur adipiscing elit. Donec hendrerit vehicula est, in</div>
<div class="abs quote-mark">&ldquo;</div>
<svg class="abs" style="left:490px;top:761px" width="18" height="12" viewBox="0 0 18 12"><path d="M0 0h18L9 12z" fill="#555"/></svg>
<div class="abs" style="left:479px;top:783px;font-size:11px;font-weight:700;color:#333">Daniel Brooks</div>
<div class="abs" style="left:479px;top:802px;font-size:7.8px;color:#333">CEO&nbsp; of&nbsp; Partner Company</div>

<!-- clients -->
<div class="abs sec-title" style="left:60px;top:860px">Our <b>Clients</b></div>
<div class="abs sq-arrow" style="left:630px;background:#e6e6e6"><svg width="19" height="18" viewBox="0 0 19 18"><path d="M11 5l-4 4 4 4" stroke="#555" stroke-width="1.5" fill="none"/></svg></div>
<div class="abs sq-arrow" style="left:652px;background:#333"><svg width="19" height="18" viewBox="0 0 19 18"><path d="M8 5l4 4-4 4" stroke="#fff" stroke-width="1.5" fill="none"/></svg></div>
<div class="abs" style="left:60px;top:886px;width:610px;height:1px;background:var(--line)"></div>

<div class="abs client" style="left:60px;font-size:16px;color:#555"><span class="dot" style="background:#c9a24a"></span>Norvale</div>
<div class="abs client" style="left:183px">Kestra</div>
<div class="abs client" style="left:273px;font-weight:400;color:#444">Lumora.com</div>
<div class="abs client" style="left:418px">Brisk</div>
<div class="abs client" style="left:496px;font-size:16px"><span class="dot"></span>Orbit</div>
<div class="abs client" style="left:563px;font-size:15px">Vantor</div>
<div class="abs client" style="left:613px;font-size:19px">Kestra</div>

<!-- footer -->
<footer class="abs footer"></footer>
<div class="abs foot-head" style="left:61px">CONTACT INFO</div>
<div class="abs foot-text" style="left:60px;top:1026px;width:140px">Office No: 12 &amp; 14, 2nd Floor, Palmgate Bldg. No. 8, Zone 22, Al Noor Street, P.O. Box: 40012, Doha, Qatar.</div>
<div class="abs foot-text" style="left:61px;top:1085px">Phone: +974 – 40001234</div>
<div class="abs foot-text" style="left:60px;top:1104px">Email: info@brightpathtalent.com</div>

<div class="abs foot-head" style="left:246px">Recent Jop Posts</div>
<div class="abs foot-post" style="left:246px;top:1020px;width:170px">DUNEMARK AIRWAYS SSP - Recruitment Drive India</div>
<div class="abs foot-date" style="left:246px;top:1054px">Sunday, October 27, 2013</div>
<div class="abs" style="left:246px;top:1073px;width:164px;height:1px;background:#444"></div>
<div class="abs foot-post" style="left:246px;top:1084px;width:170px">DUNEMARK AIRWAYS SSP - Recruitment Drive India</div>
<div class="abs foot-date" style="left:246px;top:1118px">Sunday, October 27, 2013</div>

<div class="abs foot-head" style="left:437px">Subscribe to our Newsletter</div>
<div class="abs" style="left:437px;top:1021px;width:126px;height:26px;background:#3a3a3a;font-size:8.6px;color:#aaa;line-height:26px;padding-left:10px">Enter Your Mail Id</div>
<div class="abs btn foot-btn" style="left:437px;top:1060px;width:75px;height:26px;line-height:26px">Subscribe</div>

<div class="abs foot-head" style="left:589px">Follow Us</div>
<div class="abs foot-social" style="left:588px"></div>
<div class="abs foot-social" style="left:609px"></div>
<div class="abs foot-social" style="left:630px"></div>

<div class="abs copyright">© Copyright 2014 brightpathtalent.com.&nbsp; All Rights Reserved.</div>

</body>
</html>
```